Professional & attention grabbing.

A business card design, front and back. I already have a logo I will attach, but I am open to something new as well.
Things to include:
Name:
Title:
Phone:
Email:
Wanting something that is professional but attention grabbing.
Also we do a lot of work using drones on natural gas pipelines (leading the future)if you want to include any of that. I'm open to ideas.
Target Market(s)
Natural gas transmission industry / greenhouse gas mitigation industry
Industry/Entity Type
Business
Colors
Designer to choose colors to be used in the design.
Look and feel
Each slider illustrates characteristics of the customer's brand and the style your logo design should communicate.

```html
<!DOCTYPE html>
<html lang="en">
<head>
<meta charset="UTF-8">
<title>Ridgeline Inspections – Business Card</title>
<link href="https://fonts.googleapis.com/css2?family=Lato:wght@400;700;900&display=swap" rel="stylesheet">
<style>
  :root {
    --page-bg: #e9e7e4;
    --card-bg: #f3f3f2;
    --card-edge: #d6d6d4;
    --brand-red: #a3111d;
    --brand-red-dark: #6e0710;
    --swoosh: #1b1b1b;
    --ink: #1e1e1e;
    --on-red: #f4eaea;
  }
  * { margin: 0; padding: 0; box-sizing: border-box; }
  html, body {
    width: 1200px; height: 969px; overflow: hidden;
    background: var(--page-bg);
    font-family: "Lato", Arial, sans-serif;
  }
  .card {
    position: absolute; left: 100px; top: 200px;
    width: 1000px; height: 568px;
    border-radius: 38px; overflow: hidden;
    background: var(--card-bg);
    border: 2px solid var(--card-edge);
    box-shadow: 0 18px 40px rgba(0,0,0,.15);
  }
  .card__art { position: absolute; inset: 0; }
  .contact {
    position: absolute; left: 60px; top: 36px;
    color: var(--on-red);
  }
  .contact__name { font-weight: 700; font-size: 37px; letter-spacing: 1px; }
  .contact__title { font-weight: 400; font-size: 27px; margin-top: 6px; opacity: .92; }
  .contact__list { list-style: none; margin-top: 30px; }
  .contact__item {
    display: flex; align-items: center; gap: 16px;
    font-size: 27px; line-height: 38px;
  }
  .contact__icon { width: 22px; height: 22px; fill: var(--on-red); flex: none; }
  .brand {
    position: absolute; left: 480px; top: 400px;
    display: flex; align-items: center; gap: 18px;
  }
  .brand__square { width: 44px; height: 44px; background: var(--brand-red); }
  .brand__name {
    font-weight: 900; font-size: 50px; color: var(--ink);
    letter-spacing: 1px; text-transform: uppercase;
  }
</style>
</head>
<body>
  <div class="card">
    <svg class="card__art" viewBox="0 0 1000 568" width="1000" height="568">
      <defs>
        <linearGradient id="redPanel" x1="0" y1="0" x2="1" y2="1">
          <stop offset="0" stop-color="var(--brand-red)"/>
          <stop offset=".55" stop-color="#b31c27"/>
          <stop offset="1" stop-color="var(--brand-red-dark)"/>
        </linearGradient>
      </defs>
      <path class="red-panel" fill="url(#redPanel)"
            d="M0 0 H1000 V8 C930 90 840 230 690 262 C520 300 290 240 40 548 L0 568 Z"/>
      <path class="swoosh" fill="var(--swoosh)"
            d="M40 548 C290 240 520 300 690 262 C840 230 930 90 1000 8 V22
               C940 120 860 262 700 292 C520 326 300 290 40 548 Z"/>
    </svg>

    <div class="contact">
      <div class="contact__name">DANIEL MARSH</div>
      <div class="contact__title">CEO/Founder</div>
      <ul class="contact__list">
        <li class="contact__item">
          <svg class="contact__icon" viewBox="0 0 24 24"><path d="M6.6 10.8a15.1 15.1 0 0 0 6.6 6.6l2.2-2.2c.3-.3.7-.4 1-.2 1.1.4 2.3.6 3.6.6.6 0 1 .4 1 1V20c0 .6-.4 1-1 1A17 17 0 0 1 3 4c0-.6.4-1 1-1h3.5c.6 0 1 .4 1 1 0 1.3.2 2.5.6 3.6.1.3 0 .7-.2 1z"/></svg>
          614 555 0172
        </li>
        <li class="contact__item">
          <svg class="contact__icon" viewBox="0 0 24 24"><path d="M2 5h20v14H2z M3.5 6.5 12 13l8.5-6.5" stroke="var(--brand-red)" stroke-width="1.5"/></svg>
          hello@ridgeline.com
        </li>
        <li class="contact__item">
          <svg class="contact__icon" viewBox="0 0 24 24"><circle cx="12" cy="12" r="10"/><path d="M2 12h20M12 2c3 3 3 17 0 20M12 2c-3 3-3 17 0 20" stroke="var(--brand-red)" stroke-width="1.4" fill="none"/></svg>
          www.ridgeline.com
        </li>
      </ul>
    </div>

    <div class="brand">
      <span class="brand__square"></span>
      <span class="brand__name">Ridgeline Inspections</span>
    </div>
  </div>
</body>
</html>
```